Flyer Design Project for lawn care business

I need a flyer designed for my lawn care business, "Fenwick's Upkeep Services".  It is a family owned small landscaping company. I was thinking something that I can print  2- 3 per page.
I have  2 different logos I can upload to give an idea.  I have seen some I like that are colorfull with neat graphics but I also like some that are simple and elegant.  I would like something that catches your eye and looks professionaly done.

Target Market(s)
Homeowners in Durham, North Carolina with homes usually valued $200,000 or more.
Industry/Entity Type
Landscaping
Requirements
Must have
- I would like the address of my website listed on it, www.fenwickupkeepservices-example.com
I would like for it to say somewhere, 50% off first service with seasonal service.
Not sure if I want to list some of the services that I offer or just say full service lawn care.
Nice to have
- I have a logo with a bull pushing a lawn mower.  I live in Durham, NC also known as the Bull City.  I am not in love with the logo so feel free to change it or not use it at all.

```html
<!DOCTYPE html>
<html lang="en">
<head>
<meta charset="utf-8">
<title>Fenwicks – Full Service Lawn Care Flyer</title>
<link rel="stylesheet" href="https://fonts.googleapis.com/css2?family=Jost:wght@500;600;700&display=swap">
<style>
  :root {
    --gutter: #0a0a0a;
    --panel: #ffffff;
    --brand-green: #7cfc00;
    --offer-red: #ff0a0a;
    --url-white: #ffffff;
    --grass-deep: #1f6a12;
    --grass-mid: #3f9e1e;
    --grass-bright: #6cc22a;
    --grass-light: #a2dc5a;
    --sky: #2f6fd2;
    --sky-light: #a9cdf2;
    --hedge: #24501a;
    --hedge-dark: #163a10;
    --soil: #6b5a44;
  }
  html, body {
    margin: 0;
    padding: 0;
    width: 1200px;
    height: 932px;
    overflow: hidden;
    background: var(--panel);
  }
  .flyer {
    position: relative;
    width: 1200px;
    height: 932px;
    background: var(--gutter);
    overflow: hidden;
    font-family: "Jost", "Century Gothic", sans-serif;
  }
  .photo {
    position: absolute;
    background: linear-gradient(160deg, var(--grass-light), var(--grass-mid) 55%, var(--grass-deep));
  }
  .photo--hedge { background: linear-gradient(170deg, var(--hedge-dark), var(--hedge) 45%, var(--grass-mid)); }
  .photo--leaves { background: linear-gradient(135deg, var(--grass-bright), var(--grass-deep) 50%, var(--grass-light)); }
  .photo--gardener { background: linear-gradient(90deg, var(--hedge) 0%, var(--grass-mid) 30%, var(--sky-light) 55%, var(--sky) 100%); }
  .photo--boots { background: linear-gradient(180deg, var(--soil) 0%, var(--grass-bright) 40%, var(--grass-deep) 100%); }
  .photo--sprinkler { background: radial-gradient(ellipse at 70% 30%, var(--grass-light), var(--grass-mid) 55%, var(--grass-deep)); }
  .photo--bed { background: linear-gradient(180deg, #d7ddd2 0%, var(--grass-mid) 45%, var(--hedge) 100%); }
  .photo--pruning { background: linear-gradient(200deg, var(--hedge-dark), var(--grass-mid) 55%, #b3402e 100%); }
  .photo--sky { background: linear-gradient(180deg, var(--sky-light) 0%, var(--sky) 40%, var(--grass-bright) 62%, var(--grass-deep) 100%); }
  .photo--trimmer { background: linear-gradient(135deg, var(--grass-light), var(--grass-bright) 45%, var(--grass-mid)); }
  .photo--mower { background: linear-gradient(180deg, var(--sky) 0%, var(--sky-light) 28%, var(--grass-bright) 50%, var(--grass-mid) 75%, var(--grass-deep) 100%); }
  .photo--shears { background: linear-gradient(160deg, var(--grass-bright), var(--grass-mid) 50%, var(--grass-deep)); }
  .photo--spade { background: linear-gradient(180deg, var(--grass-mid), var(--grass-light) 50%, var(--grass-deep)); }
  .photo--path { background: linear-gradient(180deg, var(--hedge) 0%, var(--grass-bright) 50%, #a9b8a0 100%); }

  .title-panel {
    position: absolute;
    left: 0; top: 82px;
    width: 915px; height: 281px;
    background: var(--panel);
    text-align: center;
    color: var(--brand-green);
  }
  .title-panel__name {
    margin: 0;
    padding-top: 22px;
    font-size: 168px;
    font-weight: 600;
    line-height: 1;
    letter-spacing: -1px;
  }
  .title-panel__tagline {
    margin: 4px 0 0;
    font-size: 76px;
    font-weight: 500;
    line-height: 1;
  }

  .offer {
    position: absolute;
    left: 772px; top: 532px;
    width: 426px; height: 287px;
    background: var(--panel);
    color: var(--offer-red);
    text-align: center;
  }
  .offer__headline {
    margin: 10px 0 2px;
    font-size: 92px;
    font-weight: 600;
    line-height: 1;
    letter-spacing: -2px;
  }
  .offer__terms {
    margin: 0;
    font-size: 62px;
    font-weight: 600;
    line-height: 0.9;
  }

  .website {
    position: absolute;
    left: 0; right: 0;
    top: 850px;
    margin: 0;
    text-align: center;
    color: var(--url-white);
    font-size: 42px;
    font-weight: 500;
    line-height: 1;
    text-shadow: 0 1px 3px rgba(0,0,0,0.45);
  }
</style>
</head>
<body>
<main class="flyer">
  <div class="photo photo--hedge" style="left:0;top:0;width:350px;height:82px" role="img" aria-label="Trimmed hedges"></div>
  <div class="photo photo--leaves" style="left:358px;top:0;width:362px;height:82px" role="img" aria-label="Gloved hand planting ground cover"></div>
  <div class="photo photo--gardener" style="left:729px;top:0;width:461px;height:296px" role="img" aria-label="Gardener trimming a tall hedge"></div>
  <div class="photo photo--boots" style="left:0;top:363px;width:346px;height:120px" role="img" aria-label="Worker's boots on fresh lawn"></div>
  <div class="photo photo--sprinkler" style="left:358px;top:363px;width:362px;height:120px" role="img" aria-label="Sprinkler watering grass"></div>
  <div class="photo photo--bed" style="left:729px;top:304px;width:230px;height:182px" role="img" aria-label="Landscaper tending a flower bed"></div>
  <div class="photo photo--pruning" style="left:968px;top:304px;width:226px;height:228px" role="img" aria-label="Pruning shears cutting a branch"></div>
  <div class="photo photo--sky" style="left:0;top:493px;width:224px;height:187px" role="img" aria-label="Tall grass against blue sky"></div>
  <div class="photo photo--trimmer" style="left:234px;top:493px;width:294px;height:187px" role="img" aria-label="String trimmer edging a lawn"></div>
  <div class="photo photo--mower" style="left:537px;top:493px;width:300px;height:439px" role="img" aria-label="Man pushing a lawn mower"></div>
  <div class="photo photo--leaves" style="left:846px;top:493px;width:352px;height:187px" role="img" aria-label="Manicured lawn"></div>
  <div class="photo photo--shears" style="left:0;top:689px;width:350px;height:243px" role="img" aria-label="Gardener clipping grass with shears"></div>
  <div class="photo photo--spade" style="left:358px;top:689px;width:170px;height:243px" role="img" aria-label="Spade beside a lawn edge"></div>
  <div class="photo photo--path" style="left:846px;top:689px;width:352px;height:243px" role="img" aria-label="Garden path with shrubs"></div>

  <header class="title-panel">
    <h1 class="title-panel__name">FENWICKS</h1>
    <p class="title-panel__tagline">full service lawn care</p>
  </header>

  <section class="offer">
    <p class="offer__headline">50%OFF</p>
    <p class="offer__terms">first service<br>with seasonal<br>service</p>
  </section>

  <p class="website">www.fenwickupkeepservices-example.com</p>
</main>
</body>
</html>
```